Verodex business card

Business card for sustainable investment company called "Verodex". Verodex is an exchange platform selling carbon credits between buyers and sellers. Carbon Credits are an environmental commodity for reducing global carbon emissions.

the card should obviously have our logo and the theme should be sustainability/environment mixed with a trading platform.

Contact Information for Business Card

Logo, Name, Title, Phone, Email

Colors
0054AA
0677BA
7BADD7
CADEEF
E8F1F8
0094D4
00A9DD
6FCCEA
C7EBF8
E9F6FB
00AB8E
00BBA5
67D7C9
C6EFE9
E9F9F6
59FF00
82FF00
B8FF75
E3FFCB
F4FFEA

```html
<!DOCTYPE html>
<html lang="en">
<head>
<meta charset="utf-8">
<title>Verodex business card</title>
<link href="https://fonts.googleapis.com/css2?family=Lexend:wght@400;500;600;700&display=swap" rel="stylesheet">
<style>
  :root {
    --page-bg: #e7e7e6;
    --navy: #1d2b45;
    --navy-deep: #172339;
    --navy-light: #2c3d5b;
    --card-white: #f1f1f1;
    --ink: #1d2b45;
    --teal: #4cbccf;
    --blue: #2f6cc0;
    --white: #ffffff;
  }
  * { box-sizing: border-box; margin: 0; padding: 0; }
  html, body {
    width: 1200px; height: 1200px; overflow: hidden;
    background: var(--page-bg);
    font-family: "Lexend", sans-serif;
  }
  .card {
    position: absolute;
    left: 233px;
    width: 732px;
    height: 418px;
    overflow: hidden;
  }
  .card-front { top: 160px; }
  .card-back { top: 632px; background: linear-gradient(135deg, #e6e6e6, var(--card-white)); }

  .front-pattern {
    position: absolute; inset: 0;
    background: linear-gradient(100deg, var(--navy-deep) 0%, var(--navy) 50%, var(--navy-light) 100%);
  }
  .front-wordmark {
    position: absolute;
    left: 0; right: 0; top: 0; bottom: 0;
    display: flex; align-items: center; justify-content: center; gap: 16px;
  }
  .front-wordmark .mark-dot {
    width: 34px; height: 34px; border-radius: 50%;
    background: var(--white);
  }
  .front-wordmark .name {
    color: var(--white);
    font-weight: 600;
    font-size: 40px;
    letter-spacing: 0.5px;
  }

  .back-wordmark {
    position: absolute;
    left: 186px; top: 76px;
    width: 350px;
    display: flex; align-items: center; gap: 18px;
  }
  .back-wordmark .mark-dot {
    width: 54px; height: 54px; border-radius: 50%;
    background: var(--blue);
  }
  .back-wordmark .name {
    color: var(--ink);
    font-weight: 600;
    font-size: 46px;
    letter-spacing: 0.5px;
  }

  .office {
    position: absolute;
    left: 56px; top: 198px;
    color: var(--ink);
    font-size: 19px;
    line-height: 1.4;
  }
  .office-title { font-weight: 700; font-size: 19px; }
  .contact-list { list-style: none; margin-top: 8px; }
  .contact-list li {
    display: flex; align-items: center; gap: 8px;
    font-size: 20px; line-height: 28px;
  }
  .contact-list svg { width: 16px; height: 16px; flex: none; }

  .person {
    position: absolute;
    right: 57px; top: 238px;
    text-align: right;
  }
  .person-name {
    font-weight: 700;
    font-size: 31px;
    line-height: 1.1;
    background: linear-gradient(90deg, var(--teal), var(--blue));
    -webkit-background-clip: text; background-clip: text;
    color: transparent;
  }
  .person-title {
    color: var(--ink);
    font-size: 19px;
    margin-top: 6px;
  }
  .footer-band { position: absolute; left: 0; bottom: 0; width: 732px; height: 60px; }
</style>
</head>
<body>
  <section class="card card-front">
    <div class="front-pattern" role="img" aria-label="Embossed repeating brand mark pattern on navy"></div>
    <div class="front-wordmark">
      <span class="mark-dot"></span>
      <span class="name">VERODEX</span>
    </div>
  </section>

  <section class="card card-back">
    <div class="back-wordmark">
      <span class="mark-dot"></span>
      <span class="name">VERODEX</span>
    </div>

    <div class="office">
      <p class="office-title">Verodex Head Office</p>
      <p class="office-address">Budapest XIII. Forgó utca 12.</p>
      <ul class="contact-list">
        <li>
          <svg viewBox="0 0 16 16" aria-hidden="true"><path fill="#3a8fc8" d="M3.5 1.5l2.5 2.8-1.4 1.6c.9 2 2.5 3.6 4.5 4.5l1.6-1.4 2.8 2.5-1.6 2.2C6.8 13.6 2.4 9.2 1.3 3.1z"/></svg>
          <span>+36 30 555 0142</span>
        </li>
        <li>
          <svg viewBox="0 0 16 16" aria-hidden="true"><rect x="1" y="3" width="14" height="10" rx="1" fill="#3a8fc8"/><path d="M1.5 4l6.5 5 6.5-5" fill="none" stroke="#fff" stroke-width="1.2"/></svg>
          <span>szerviz@verodex.com</span>
        </li>
        <li>
          <svg viewBox="0 0 16 16" aria-hidden="true"><g fill="none" stroke="#3a8fc8" stroke-width="1.4"><circle cx="8" cy="8" r="6.5"/><ellipse cx="8" cy="8" rx="2.8" ry="6.5"/><path d="M1.5 8h13"/></g></svg>
          <span>www.verodex.com</span>
        </li>
      </ul>
    </div>

    <div class="person">
      <p class="person-name">Mark Halden</p>
      <p class="person-title">Sales Representative</p>
    </div>

    <svg class="footer-band" viewBox="0 0 732 60" preserveAspectRatio="none" aria-hidden="true">
      <path d="M0 24 H455 C470 24 475 4 495 4 H732 V60 H0 Z" fill="var(--navy)"/>
      <path d="M0 38 H430 C450 38 462 30 470 24 H0 Z" fill="var(--navy-deep)" opacity="0.6"/>
    </svg>
  </section>
</body>
</html>
```